Design eines Zertifikats
Ich bin total begeistert. Super Kommunikation, super schnelle Reaktion auf kleine Änderungswünsche, ich bin wirklich rundum zufrieden!! Auch bei weiterführenden Fragen die gar nicht direkt mit dem Design zusammenhingen wurde mir total schnell und sympathisch geholfen, ich kann die Designerin nur wärmstens weiterempfehlen!
Zielgruppe
Ich betreibe einen Onlineshop, in dem ich sogenannte Sterntaufen verkaufe. Ein Kunde bekommt dabei im Zuge seines Kaufes ein Zertifikat ausgestellt mit Daten zu seinem getauften Stern. Es geht hier um das Design eines neuen Zertifikats um möglichst noch mehr Käufer anzusprechen. Es sind bereits 3 Designs vorhanden, das neue sollte sich entsprechend etwas absetzen.
Ich lasse die Zertifikate in einer Druckerei drucken, und bedrucke diese dann selber mit den Daten der Sterntaufe, es muss auf dem Zertifikat also ein heller Bereich vorhanden sein in dem ich drucken kann.
Aufgabenstellung
Das Zertifikat soll A4 sein. Es sollte modern sein und sich wie gesagt möglichst von den bestehenden absetzen, und ein möglichst breites Publikum ansprechen.
Beispiele für Zertifikate der Konkurrenz finden sich unter:
himmelspunkt17.de
nebelverzeichnis.de
lichtpate-bundesweit.de
Das von himmelspunkt17.de gefällt mir persönlich ganz gut, aber lasst euch nicht von den Vorschlägen einschränken.
Bitte nicht zu exzessiv kostenpflichtiges Stockmaterial verwenden, ich mache leider aktuell noch Miese mit dem Shop :-)
Bitte schaut auf meine Webseite um ein Gefühl dafür zu bekommen wie viel Platz für Text vorhanden sein muss.

```html
<!DOCTYPE html>
<html lang="de">
<head>
<meta charset="utf-8">
<title>Sternen Urkunde</title>
<link rel="stylesheet" href="https://fonts.googleapis.com/css2?family=Cinzel:wght@600&family=Allura&display=swap">
<style>
  :root {
    --navy-deep: #13233f;
    --navy: #1b3050;
    --navy-mid: #233f5e;
    --ribbon-blue: #27466a;
    --paper: #f7f7f9;
    --paper-shade: #d9dbe3;
    --gold-light: #f8d873;
    --gold: #e2ad45;
    --gold-dark: #c27a1c;
  }
  html, body {
    margin: 0;
    padding: 0;
    overflow: hidden;
    background: #ffffff;
  }
  .certificate {
    position: relative;
    width: 1200px;
    height: 848px;
    overflow: hidden;
    background: linear-gradient(135deg, var(--paper-shade) 0%, var(--paper) 45%, #ffffff 70%, var(--paper-shade) 100%);
  }
  .certificate__backdrop {
    position: absolute;
    inset: 0;
    width: 1200px;
    height: 848px;
  }
  .certificate__title {
    position: absolute;
    left: 82px;
    top: 62px;
    margin: 0;
    font-family: "Cinzel", "Times New Roman", serif;
    font-weight: 600;
    font-size: 90px;
    line-height: 1;
    letter-spacing: 0;
    background: linear-gradient(180deg, var(--gold-light) 0%, var(--gold) 45%, var(--gold-dark) 75%, var(--gold-light) 100%);
    -webkit-background-clip: text;
    background-clip: text;
    color: transparent;
    filter: drop-shadow(2px 2px 1px rgba(0, 0, 0, 0.45));
  }
  .certificate__subtitle {
    position: absolute;
    left: 108px;
    top: 150px;
    margin: 0;
    font-family: "Allura", cursive;
    font-weight: 400;
    font-size: 84px;
    line-height: 1;
    color: var(--gold);
  }
  .certificate__seal {
    position: absolute;
    left: 97px;
    top: 474px;
    width: 240px;
    height: 240px;
    border-radius: 50%;
    background: radial-gradient(circle at 45% 40%, var(--gold-light) 0%, var(--gold) 55%, var(--gold-dark) 100%);
  }
</style>
</head>
<body>
  <main class="certificate">
    <svg class="certificate__backdrop" viewBox="0 0 2296 1623" preserveAspectRatio="none" aria-hidden="true">
      <defs>
        <linearGradient id="ribbon-fill" x1="0" y1="0" x2="0" y2="1">
          <stop offset="0" stop-color="var(--ribbon-blue)"/>
          <stop offset="1" stop-color="var(--navy)"/>
        </linearGradient>
        <linearGradient id="band-fill" x1="0" y1="0" x2="1" y2="0">
          <stop offset="0" stop-color="var(--navy-deep)"/>
          <stop offset="1" stop-color="var(--navy-mid)"/>
        </linearGradient>
        <linearGradient id="swoosh-fill" x1="0" y1="0" x2="1" y2="0">
          <stop offset="0" stop-color="var(--gold-dark)"/>
          <stop offset="0.4" stop-color="var(--gold-light)"/>
          <stop offset="0.8" stop-color="var(--gold-dark)"/>
          <stop offset="1" stop-color="var(--gold)"/>
        </linearGradient>
      </defs>

      <g class="side-ribbon">
        <rect x="232" y="600" width="369" height="1023" fill="url(#ribbon-fill)"/>
        <rect x="260" y="600" width="6" height="1023" fill="var(--gold-dark)"/>
        <rect x="566" y="600" width="6" height="1023" fill="var(--gold-dark)"/>
      </g>

      <path class="band band--outer" fill="var(--navy-mid)"
            d="M0,830 C400,820 900,560 1300,410 C1700,265 2000,235 2296,285 V0 H0 Z"/>
      <path class="band band--inner" fill="url(#band-fill)"
            d="M0,632 C500,640 900,420 1300,300 C1700,190 2000,170 2296,220 V0 H0 Z"/>
      <path class="band band--edge" fill="var(--navy-deep)"
            d="M1250,318 C1650,195 2000,172 2296,220 V250 C2000,205 1650,215 1250,335 Z"/>

      <path class="swoosh swoosh--shadow" fill="var(--gold-dark)"
            d="M1413,362 C1750,300 2080,315 2296,440 V480 C2100,345 1750,315 1413,362 Z"/>
      <path class="swoosh" fill="url(#swoosh-fill)"
            d="M1413,362 C1700,262 2050,250 2296,282 V440 C2080,315 1750,300 1413,362 Z"/>
    </svg>

    <h1 class="certificate__title">STERNEN</h1>
    <p class="certificate__subtitle">Urkunde</p>

    <div class="certificate__seal" role="img" aria-label="Goldenes Siegel mit Stern und Schleifenbändern"></div>
  </main>
</body>
</html>
```